Mobile app for checking bus arrival

I would like to make the UI much more beautiful and modern. The app is an app to check bus arrival in Singapore.
See here: https://apps.veltrano.com/store/apps/details?id=com.ridoka&hl=en

Based on the question from designers:

1. The first screen shows the favorite bus stop. Each item shows location / street, the top one is the location, second line is the street name. And the number is the bus stop code.

2. Please download the app and try bus stop code with 07589 or 10079, for example. It will bring you to the next screen.

3. The pencil allow you to select color theme, for the list item, and the header.

4. On the second screen, it will show up the list of bus route that available on that bus stop.

5. When you tap on one of them it will show you the 2 subsequent arrival time.

6. Each of the arrival time has the information of availability seats available, seats not available, no more space. (we can use green, yellow, red, respectively).

7. Each of the arrival time has the WAB indicator (Wheelchair availability). Show as icon is preferred.

7. KLT and VOPN are the bus provider in Singapore. 48 means the route /service no.

Requirements:
And check the attachment, see screen 3. I need to add information about the space availability, which has 3 state: seats available, seats not available, no more space. (we can use green, yellow, red, respectively).

Please advise how to show the information.

Target Market(s)

Students, age below 35

Industry/Entity Type

Trivex

Requirements
Must have
• The app currently has the capabilities to select color theme, checkout screen1. It's the button and the list item color.
Nice to have
• Please download the app to see all available colors, and make suggestion to have better color pallete.

```html
<!DOCTYPE html>
<html lang="en">
<head>
<meta charset="utf-8">
<title>Bus Arrival – Favorites</title>
<link rel="stylesheet" href="https://fonts.googleapis.com/css2?family=Roboto:wght@400;500&display=swap">
<style>
  :root {
    --page-bg: #e4e4e4;
    --status-bar: #4b2a8a;
    --app-bar: #673ab7;
    --accent: #673ab7;
    --badge: #6a3cbc;
    --map-tone: #e8e4da;
    --map-tone-2: #ddd8cc;
    --header-bg: #eff3f6;
    --surface: #ffffff;
    --divider: #e7e7e7;
    --title-text: #555a60;
    --sub-text: #b9bcbf;
    --placeholder: #a9a9a9;
    --star: #f9a825;
    --pin: #e5224b;
    --me: #4f7cff;
  }
  * { box-sizing: border-box; margin: 0; padding: 0; }
  html, body { width: 960px; height: 1200px; overflow: hidden; }
  body { background: var(--page-bg); font-family: "Roboto", sans-serif; position: relative; }

  .screen { position: absolute; left: 156px; top: 24px; width: 648px; height: 1152px; background: var(--surface); overflow: hidden; }

  .status-bar { position: absolute; top: 0; left: 0; right: 0; height: 44px; background: var(--status-bar); color: #fff; display: flex; align-items: center; justify-content: flex-end; gap: 12px; padding-right: 16px; }
  .status-bar .clock { font-size: 23px; letter-spacing: 0.5px; }

  .app-bar { position: absolute; top: 44px; left: 0; right: 0; height: 100px; background: var(--app-bar); }
  .menu-button { position: absolute; left: 34px; top: 35px; }
  .search-box { position: absolute; left: 102px; top: 16px; width: 528px; height: 69px; background: #fff; border-radius: 2px; box-shadow: 0 1px 3px rgba(0,0,0,.2); display: flex; align-items: center; }
  .search-box .search-icon { margin-left: 32px; }
  .search-box .placeholder { margin-left: 18px; font-size: 25px; color: var(--placeholder); flex: 1; }
  .search-box .mic-icon { margin-right: 30px; }

  .map { position: absolute; top: 144px; left: 0; right: 0; height: 371px; background: linear-gradient(135deg, var(--map-tone) 0%, var(--map-tone-2) 100%); }
  .locate-button { position: absolute; left: 559px; top: 162px; width: 72px; height: 72px; border-radius: 50%; background: #fff; box-shadow: 0 1px 4px rgba(0,0,0,.25); display: flex; align-items: center; justify-content: center; }
  .stop-popup { position: absolute; left: 227px; top: 265px; width: 195px; height: 69px; background: var(--accent); border-radius: 3px; color: #fff; padding: 10px 0 0 13px; box-shadow: 0 2px 4px rgba(0,0,0,.2); }
  .stop-popup .name { font-size: 16px; font-weight: 500; }
  .stop-popup .code { font-size: 25px; margin-top: 2px; }
  .stop-popup .go { position: absolute; right: 12px; top: 21px; }
  .stop-popup::after { content: ""; position: absolute; left: 90px; bottom: -8px; border: 8px solid transparent; border-top-color: var(--accent); border-bottom: 0; }
  .stop-pin { position: absolute; left: 314px; top: 344px; }
  .my-location { position: absolute; left: 163px; top: 365px; width: 24px; height: 24px; border-radius: 50%; background: var(--me); border: 4px solid #fff; box-shadow: 0 0 0 8px rgba(79,124,255,.2); }

  .fab { position: absolute; left: 513px; top: 464px; width: 102px; height: 102px; border-radius: 50%; background: var(--accent); box-shadow: 0 4px 10px rgba(0,0,0,.3); display: flex; align-items: center; justify-content: center; z-index: 2; }

  .section-header { position: absolute; top: 515px; left: 0; right: 0; height: 108px; background: var(--header-bg); border-bottom: 1px solid var(--divider); }
  .section-header h1 { position: absolute; left: 32px; top: 38px; font-size: 38px; font-weight: 400; color: #4f555b; }

  .favorite-list { position: absolute; top: 623px; left: 0; right: 0; list-style: none; }
  .favorite-item { position: relative; height: 120px; border-bottom: 1px solid var(--divider); background: var(--surface); }
  .stop-code { position: absolute; left: 33px; top: 35px; width: 97px; height: 51px; background: var(--badge); color: #fff; font-size: 24px; display: flex; align-items: center; justify-content: center; border-radius: 2px; }
  .stop-name { position: absolute; left: 152px; top: 28px; font-size: 24px; color: var(--title-text); }
  .stop-street { position: absolute; left: 152px; top: 64px; font-size: 21px; color: var(--sub-text); }
  .favorite-star { position: absolute; left: 569px; top: 44px; }
</style>
</head>
<body>
  <div class="screen">
    <div class="status-bar">
      <svg width="22" height="22" viewBox="0 0 22 22"><path d="M2 20 L20 2 V20 Z" fill="#fff" opacity=".5"/><path d="M2 20 L14 8 V20 Z" fill="#fff"/></svg>
      <svg width="16" height="24" viewBox="0 0 16 24"><rect x="2" y="2" width="12" height="21" rx="1" fill="#fff" opacity=".5"/><rect x="2" y="11" width="12" height="12" fill="#fff"/><rect x="5" y="0" width="6" height="3" fill="#fff" opacity=".5"/></svg>
      <span class="clock">12:30</span>
    </div>

    <header class="app-bar">
      <svg class="menu-button" width="34" height="28" viewBox="0 0 34 28"><rect y="3" width="34" height="3" fill="#fff"/><rect y="12" width="34" height="3" fill="#fff"/><rect y="21" width="34" height="3" fill="#fff"/></svg>
      <div class="search-box">
        <svg class="search-icon" width="32" height="32" viewBox="0 0 32 32"><circle cx="12.5" cy="12.5" r="9" fill="none" stroke="#9e9e9e" stroke-width="3"/><path d="M19 19 L29 29" stroke="#9e9e9e" stroke-width="3.5" stroke-linecap="round"/></svg>
        <span class="placeholder">Bus Stop Code</span>
        <svg class="mic-icon" width="24" height="34" viewBox="0 0 24 34"><rect x="7" y="1" width="10" height="20" rx="5" fill="#9e9e9e"/><path d="M2 15 a10 10 0 0 0 20 0" fill="none" stroke="#9e9e9e" stroke-width="2.5"/><rect x="10.8" y="25" width="2.5" height="8" fill="#9e9e9e"/></svg>
      </div>
    </header>

    <div class="map" role="img" aria-label="Street map around the selected bus stop with nearby roads, canal and landmarks">
      <div class="locate-button">
        <svg width="36" height="36" viewBox="0 0 36 36"><circle cx="18" cy="18" r="10" fill="none" stroke="#666" stroke-width="2.5"/><circle cx="18" cy="18" r="5" fill="#666"/><path d="M18 2 V8 M18 28 V34 M2 18 H8 M28 18 H34" stroke="#666" stroke-width="2.5"/></svg>
      </div>
      <div class="my-location"></div>
      <div class="stop-popup" style="top:121px">
        <div class="name">Opp Marlow Ctr</div>
        <div class="code">#07589</div>
        <svg class="go" width="28" height="28" viewBox="0 0 28 28"><circle cx="14" cy="14" r="12" fill="none" stroke="#fff" stroke-width="2"/><path d="M11.5 8.5 L17 14 L11.5 19.5" fill="none" stroke="#fff" stroke-width="2.2"/></svg>
      </div>
      <svg class="stop-pin" style="top:200px" width="20" height="20" viewBox="0 0 20 20"><circle cx="10" cy="10" r="9" fill="#fff" stroke="var(--pin)" stroke-width="2.5"/><circle cx="10" cy="10" r="4" fill="var(--pin)"/></svg>
    </div>

    <button class="fab" aria-label="Choose colour theme" style="border:0">
      <svg width="38" height="38" viewBox="0 0 24 24"><path d="M3 17.25V21h3.75L17.8 9.94l-3.75-3.75L3 17.25zM20.7 7.04a1 1 0 0 0 0-1.41l-2.34-2.34a1 1 0 0 0-1.41 0l-1.83 1.83 3.75 3.75 1.83-1.83z" fill="#fff"/></svg>
    </button>

    <section class="section-header"><h1>My Favorite</h1></section>

    <ul class="favorite-list">
      <li class="favorite-item"><span class="stop-code">07589</span><span class="stop-name">Opp Marlow Ctr</span><span class="stop-street">Orvin Rd</span><svg class="favorite-star" width="34" height="34" viewBox="0 0 24 24"><path d="M12 17.3l6.2 3.7-1.6-7 5.4-4.7-7.2-.6L12 2 9.2 8.7 2 9.3l5.4 4.7-1.6 7z" fill="var(--star)"/></svg></li>
      <li class="favorite-item"><span class="stop-code">12119</span><span class="stop-name">Police Alder Trg Camp</span><span class="stop-street">Ulu Kesang Rd</span><svg class="favorite-star" width="34" height="34" viewBox="0 0 24 24"><path d="M12 17.3l6.2 3.7-1.6-7 5.4-4.7-7.2-.6L12 2 9.2 8.7 2 9.3l5.4 4.7-1.6 7z" fill="var(--star)"/></svg></li>
      <li class="favorite-item"><span class="stop-code">14009</span><span class="stop-name">Bayside Int</span><span class="stop-street">Tan Kee Rd</span><svg class="favorite-star" width="34" height="34" viewBox="0 0 24 24"><path d="M12 17.3l6.2 3.7-1.6-7 5.4-4.7-7.2-.6L12 2 9.2 8.7 2 9.3l5.4 4.7-1.6 7z" fill="var(--star)"/></svg></li>
      <li class="favorite-item"><span class="stop-code">01012</span><span class="stop-name">Hotel Grand Meridel</span><span class="stop-street">Lindell St</span><svg class="favorite-star" width="34" height="34" viewBox="0 0 24 24"><path d="M12 17.3l6.2 3.7-1.6-7 5.4-4.7-7.2-.6L12 2 9.2 8.7 2 9.3l5.4 4.7-1.6 7z" fill="var(--star)"/></svg></li>
      <li class="favorite-item"><span class="stop-code">&nbsp;</span><span class="stop-name">Blk 1003</span><span class="stop-street">&nbsp;</span><svg class="favorite-star" width="34" height="34" viewBox="0 0 24 24"><path d="M12 17.3l6.2 3.7-1.6-7 5.4-4.7-7.2-.6L12 2 9.2 8.7 2 9.3l5.4 4.7-1.6 7z" fill="var(--star)"/></svg></li>
    </ul>
  </div>
</body>
</html>
```